Website development company website

ABOUT COMPANY
Hi everyone! We're a Melbourne, Australia website development company in a need of a website design that will make online store merchants want to engage our services.
We specialise exclusively in Torvista e-commerce platform (https://torvista-platform.example/). What distinguishes our business from competition is that rather than designing and building brand new websites, we offer development, support and maintenance services to established websites. Maintenance and Support are the keywords representing our business.
Our potential clients are people with broken, slow and underperforming Torvista installations who need assistance getting their websites up and making sales. Our website must pass the message that we can help, and provide quick means of making contact.
DESIGN
Overall, we're looking for a slick, clean, airy, conservative design. No need to do anything crazy, try to stick to what's "standard" in website design these days and make it easy on all of us. The website is unlikely to be updated too often so it needs to look attractive and fresh first time over and after a year, too.
Attached is our new logo, which you'll be able to take the basic idea from, the colors and fonts. Though, don't use the fonts from the logo in the website, stick to the standard widely supported fonts. Additional use of Google fonts is fine.
Don't overdo it with colors, stick to conservative basic color set and only use the colors from the log for accents like headings etc. Please, don't be tempted to use the blue and orange as background of whole blocks, other than perhaps footer. Thanks.
For the images used, I'd like to stay away from a design studio/digital agency feel and lean more towards professional support and maintenance services. I'm thinking images of content merchants doing their job. Something along the lines of "We'll be taking care of the website so that you only need to care about the business".
Some ideas I like:
http://www.plumframe-pics.example/detail/photo/portrait-of-confident-male-design-professional-royalty-free-image/572048163
http://www.plumframe-pics.example/detail/photo/designer-taking-picture-of-hat-high-res-stock-photography/839207514
http://www.plumframe-pics.example/detail/photo/woman-packaging-pottery-royalty-free-image/216684093
Images of colorful shopping bags and shopping carts are over the top and not serious enough. Instead of images matching Online Shopping, I'd try going more for Stability, Reliability, Performance.
Our existing website is http://www.bravuln.example. Please, don't take design ideas from it, but it will give you a picture of the structure of our new website and content that's going to be used initially.
If you could include a basic icon set to use throughout the website, that would be great. If the icons could match our logo (attached), it would be a big plus.
ALL PAGES
Every page must contain clearly visible phone number (1300 648 907) and a Contact Us Now button, which opens an AJAX driven popup form with Name, Email, Phone and Message to be sent through.
To start with, main menu items will be Torvista, Portfolio, Contact.
At the bottom of each page, please, include a newsletter subscription form with text Subscribe to Torvista Support and Security Updates.
For the footer, I'd like to see a logo strip with the following logos in grayscale (no need to link anywhere): Torvista, QRX, DataVane, NCB. You'll find the logos on Google Images.
Standard footer columns follow. Here, I'd like to see logos in color: Torvista Certified Developer, Torvista Ceritified Solution Provider. Again, the logos are on Google Images.
No social media logos/links necessary anywhere on the website.
...and then the copyright line.
FRONT PAGE
Large slider with images that would appeal to our target audience. Keywords here would be Torvista System Audit, Torvista Performance Optimisation, Torvista Website Emergency Recovery, Torvista Development Infrastructure Hosting. We'll have a static page created for each of these to link to.
In a corner of the slider, or on the edge, can I have an overlay with logos in color (same as footer): Torvista Certified Developer, Torvista Ceritified Solution Provider.
Underneath, a number of blocks, each with an image and teaser that we'll use to link to various pages throughout the website.
PORTFOLIO PAGE
I'm thinking a single long page with a block per client, which will contain project name, description from us and a testimonial from client. Also, each block will contain a single large screenshot. No gallery or slideshow is necessary here, just one image per project.
I'll leave the layout up to you, but try to put yourself in the shoes of a potential client reviewing our past work by simply scrolling down this one page.
CONTACT US PAGE
Separate page with the same form as above, phone number (1300 648 907), email address (support@kavreo.example), address (Suite 42, Level 3|8 Wattlebrook Lane|Fernvale Heights VIC 3999), and a grayscale Google Map.
CODING UP
Coding up into static HTML/CSS/JS is equally important as the design itself. We're a website development company, we'll be integrating the theme. We will spot any issues and we will point them out.
Coded up design must be fully responsive. Enough said.
To be able to create any content in future, we'd like one extra page coded up with samples of all themed elements, lists, forms, buttons, 2, 3, 4-column layout, alerts, icons, etc. This page does not need to be designed, only coded up.
The design will be integrated into Drupal using Twig. If possible at all, try to keep it in mind when designing and coding up, and make the integration into a Drupal theme easier for us.
GOOD LUCK!
That's it. Let me know if anything needs clarifying. So far I've had a great experience with ArtFlockly. I don't doubt some great designs will emerge. Clever ideas are highly appreciated, but also make it clear you've read and followed the points in this brief. Cheers, Tom

```html
<!DOCTYPE html>
<html lang="en">
<head>
<meta charset="utf-8">
<title>Contact Us – Kavreo E-Commerce</title>
<link rel="stylesheet" href="https://fonts.googleapis.com/css2?family=Open+Sans:wght@400;600&family=Roboto:wght@400;500&family=Roboto+Condensed:wght@700&display=swap">
<style>
:root{
  --orange:#e67f24;
  --navy:#123f6f;
  --navy-deep:#0d3562;
  --ink:#333;
  --muted:#555;
  --field:#f3f3f3;
  --field-line:#e3e3e3;
  --btn:#333;
  --white:#fff;
}
*{box-sizing:border-box;margin:0;padding:0}
html,body{width:1014px;height:1200px;overflow:hidden;background:var(--white)}
body{position:relative;font-family:"Open Sans",Arial,sans-serif;color:var(--ink)}
.abs{position:absolute}

.topbar{left:0;top:0;width:1014px;height:28px;background:var(--orange);font-family:"Roboto",Arial,sans-serif;font-size:11.5px;color:var(--white)}
.topbar-item{position:absolute;top:0;height:28px;display:flex;align-items:center;gap:7px;padding:0 14px;border-left:1px solid rgba(255,255,255,.25)}
.topbar-item:first-child{border-left:none}
.topbar-item svg{width:10px;height:10px;fill:var(--white)}

.header{left:0;top:28px;width:1014px;height:84px;background:var(--white);border-top:1px solid #d9742a}
.brand{position:absolute;left:83px;top:22px;display:flex;align-items:center;gap:8px}
.brand-mark{width:34px;height:40px;background:var(--navy)}
.brand-name{font-family:"Roboto",Arial,sans-serif;font-weight:500;font-size:30px;color:var(--orange);letter-spacing:-.5px}
.nav{position:absolute;right:85px;top:34px;display:flex;gap:26px;font-family:"Roboto",Arial,sans-serif;font-size:13.5px;color:var(--ink)}
.nav .active{color:var(--orange)}

.hero{left:0;top:112px;width:1014px;height:282px;background:linear-gradient(100deg,#5d7ea5 0%,#4b6d96 45%,#2c4d79 75%,#22426d 100%)}
.hero-title{position:absolute;left:83px;top:82px;font-family:"Roboto Condensed",Arial,sans-serif;font-weight:700;font-size:33px;color:var(--white)}
.hero-text{position:absolute;left:83px;top:130px;width:310px;font-size:12px;line-height:19px;color:var(--white)}

.field{position:absolute;background:var(--field);border:1px solid var(--field-line);font-size:11px;color:var(--muted);padding:0 13px;display:flex;align-items:center;height:31px;background:linear-gradient(#f7f7f7,#efefef)}
.field-message{align-items:flex-start;padding-top:10px;height:143px}
.send-btn{left:83px;top:719px;width:128px;height:35px;background:var(--btn);border-radius:3px;color:var(--white);font-family:"Roboto",Arial,sans-serif;font-size:14px;display:flex;align-items:center;justify-content:center}

.map{background:#dcd8d0;border:3px solid #f2f2f2}
.address-title{left:565px;top:633px;font-family:"Roboto",Arial,sans-serif;font-size:17px;color:var(--ink)}
.address-rule{left:565px;top:660px;width:264px;height:1px;background:#ddd}
.address-lines{left:567px;top:673px;font-size:11.5px;line-height:20px;color:var(--muted)}
.contact-row{position:absolute;left:568px;display:flex;align-items:center;gap:13px;font-size:11.5px;color:var(--muted)}
.contact-row svg{width:16px;height:14px;fill:none;stroke:#aaa;stroke-width:1.2}

.subscribe{left:0;top:831px;width:1014px;height:90px;background:var(--orange)}
.subscribe-text{position:absolute;left:210px;top:26px;font-family:"Roboto",Arial,sans-serif;font-size:13px;line-height:20px;color:var(--white)}
.subscribe-input{position:absolute;left:477px;top:27px;width:330px;height:36px;background:var(--white);border-radius:18px 0 0 18px;font-size:11px;color:#666;display:flex;align-items:center;padding-left:20px}
.subscribe-btn{position:absolute;left:792px;top:27px;width:106px;height:36px;background:var(--btn);border-radius:0 18px 18px 0;font-family:"Roboto",Arial,sans-serif;font-size:11.5px;color:var(--white);display:flex;align-items:center;justify-content:center}

.footer{left:0;top:921px;width:1014px;height:219px;background:var(--navy)}
.footer-brand{position:absolute;left:84px;top:30px;display:flex;align-items:center;gap:8px}
.footer-brand .brand-mark{background:var(--white)}
.footer-brand .brand-name{color:var(--white)}
.footer-about{position:absolute;left:84px;top:100px;width:260px;font-size:11px;line-height:17.5px;color:var(--white)}
.read-more{position:absolute;left:84px;top:182px;font-size:11px;color:var(--white)}
.footer-map{position:absolute;left:355px;top:33px;width:330px;height:157px;background:#d8d8d8;border-radius:2px}
.footer-heading{position:absolute;left:729px;top:32px;font-family:"Open Sans",Arial,sans-serif;font-size:14.5px;color:var(--white)}
.footer-list{position:absolute;left:727px;top:70px;list-style:none;font-size:11px;color:var(--white)}
.footer-list li{display:flex;gap:7px;line-height:21px}
.footer-list svg{width:9px;height:9px;fill:var(--orange);margin-top:6px;flex:none}
.footer-list .indent{padding-left:16px}

.copyright{left:0;top:1140px;width:1014px;height:60px;background:var(--navy-deep);font-size:10.5px;color:var(--white);display:flex;align-items:center;justify-content:center}
</style>
</head>
<body>

<div class="abs topbar">
  <div class="abs" style="left:522px;top:0;height:28px;display:flex">
    <span class="topbar-item" style="position:relative"><svg viewBox="0 0 10 10"><path d="M2 0l2 2-1 1.5c.8 1.6 2 2.8 3.5 3.5L8 6l2 2-1.5 2C4 10 0 6 0 1.5z"/></svg>Call Us + 1300 274 615</span>
    <span class="topbar-item" style="position:relative"><svg viewBox="0 0 10 10"><path d="M0 1.5h10v7H0z M1 2.5v5h8v-5L5 5.5z" fill-rule="evenodd"/></svg>info@bravuln.example</span>
    <span class="topbar-item" style="position:relative"><svg viewBox="0 0 10 10"><circle cx="5" cy="3" r="2.5"/><path d="M0.5 10c0-3 2-4.5 4.5-4.5s4.5 1.5 4.5 4.5z"/></svg>Contact Me</span>
  </div>
</div>

<header class="abs header">
  <div class="brand"><span class="brand-mark"></span><span class="brand-name">Kavreo</span></div>
  <nav class="nav">
    <span class="active">HOME</span><span>ABOUT US</span><span>PORTFOLIO</span><span>CONTACT US</span>
  </nav>
</header>

<section class="abs hero" role="img" aria-label="Photo of a businessman in a suit using a tablet">
  <h1 class="hero-title">CONTACT US</h1>
  <p class="hero-text">Lorem ipsum dolor sit amet, consectetur adipiscing elit, sed do eiusmod tempor incididunt ut labore et dolor sit amet, consectetur</p>
</section>

<form class="contact-form">
  <div class="field" style="left:84px;top:466px;width:213px">Name</div>
  <div class="field" style="left:317px;top:466px;width:213px">Phone No</div>
  <div class="field" style="left:84px;top:510px;width:213px">Mail</div>
  <div class="field" style="left:317px;top:510px;width:213px">Subjects</div>
  <div class="field field-message" style="left:84px;top:553px;width:446px">Message</div>
  <div class="abs send-btn">SEND NOW</div>
</form>

<div class="abs map" style="left:566px;top:467px;width:362px;height:151px" role="img" aria-label="Street map with a pin marking the office location"></div>

<h2 class="abs address-title">ADDRESS</h2>
<div class="abs address-rule"></div>
<p class="abs address-lines">Suite 42, Level 3|8 Wattlebrook Lane|<br>Fernvale Heights VIC 3999</p>
<div class="contact-row" style="top:723px"><svg viewBox="0 0 16 14"><path d="M3 1l3 3-1.5 2c1 2 2.5 3.5 4.5 4.5L11 9l3 3-2 2C6 14 1 8 1 3z"/></svg>Phone: +1300 648 907</div>
<div class="contact-row" style="top:746px"><svg viewBox="0 0 16 14"><rect x="1" y="2" width="14" height="10"/><path d="M1 2l7 6 7-6M1 12l5-5M15 12l-5-5"/></svg>Email: support@kavreo.example</div>

<section class="abs subscribe">
  <svg class="abs" style="left:62px;top:8px" width="86" height="76" viewBox="0 0 86 76" fill="none" stroke="rgba(255,255,255,.25)" stroke-width="3"><g transform="rotate(-28 43 38)"><rect x="10" y="16" width="66" height="44" rx="4"/><path d="M10 18l33 24 33-24"/></g></svg>
  <svg class="abs" style="left:164px;top:27px" width="33" height="33" viewBox="0 0 33 33" fill="none" stroke="#fff" stroke-width="2.5" stroke-linejoin="round"><path d="M31 2L2 15l10 4 4 11 4-8 9 5z M12 19L31 2 20 22"/></svg>
  <p class="subscribe-text">SUBSCRIBE TO TORVISTA SUPPORT AND<br>SECURITY UPDATES</p>
  <div class="subscribe-input">Enter your E - mail</div>
  <div class="subscribe-btn">SUBSCRIBE</div>
</section>

<footer class="abs footer">
  <div class="footer-brand"><span class="brand-mark"></span><span class="brand-name">Kavreo</span></div>
  <p class="footer-about">Sed ut perspiciatis unde omnis iste natus error sit voluptatem accusantium doloremque laudantium, totam rem aperiam, eaque ipsa quae ab illo inven tore veritatis et quasi architecto beatae</p>
  <span class="read-more">Read More</span>
  <div class="footer-map" role="img" aria-label="Grayscale street map with an orange pin at the office"></div>
  <h3 class="footer-heading">COMPANY ADDRESS</h3>
  <ul class="footer-list">
    <li><svg viewBox="0 0 10 10"><path d="M5 0a3.5 3.5 0 0 0-3.5 3.5C1.5 6 5 10 5 10s3.5-4 3.5-6.5A3.5 3.5 0 0 0 5 0z"/></svg>Suite 42, Level 3|8 Wattlebrook Lane|</li>
    <li class="indent">Fernvale Heights VIC 3999</li>
    <li><svg viewBox="0 0 10 10"><path d="M2 0l2 2-1 1.5c.8 1.6 2 2.8 3.5 3.5L8 6l2 2-1.5 2C4 10 0 6 0 1.5z"/></svg>Phone:&nbsp; (1300 648 907)</li>
    <li><svg viewBox="0 0 10 10"><path d="M0 2h10v6H0z"/></svg>Email: support@kavreo.example</li>
  </ul>
</footer>

<div class="abs copyright">© 2016 All copyrights Reserved. Kavreo E-Commerce</div>

</body>
</html>
```